Create the design of Sitelaunch (in photoshop or similar)

*edit* What we wanna see is a sketch of a first page, and then in the end 5 page designs, but the main page will be the big tasks other pages are just basically pop-ups or form. *edit*

We need a web design for our new startup Sitelaunch in turn will be providing web pages to smaller business. So the purpose of the page is to clearly showcase the message in a web 3.0 fashion, good design looks but function should always be the main focus.Further more we are looking for a long term relationship with a good designer / design company that can help us design the future web sites for our customers as well.

We need you to understand web, not just design. You need to be up to date with how web looks and works, and how to make it as simple and easy to use as possible for the customer and at the same time good looking.

Colors and layout are free to choose, but we really like the kind of layout that forkcomet.com has so feel free to be inspired by them.

We want all of the pages design, but the main/landing page will be the big part, the rest are small pages that will use the same design frame as the main page.

PS. We just want the design in photoshop or illustrator format, the website will then be built in word press by word press experts (let us know if you/company also possess this knowledge)

Target Market(s)

Small to medium sized business, mostly owner/entrepreneur driven companies.

Industry/Entity Type

Business

Font styles to use
Other font styles liked:
• Helvetica for the win

Requirements
Must have
• Great and simple design, a child should be able to understand the message and also enjoy reading it. Should be a funny website while still being professional, i.e. see postbadger.com for example.

```html
<!DOCTYPE html>
<html lang="en">
<head>
<meta charset="utf-8">
<title>Sitelaunch</title>
<link href="https://fonts.googleapis.com/css2?family=Roboto+Condensed:wght@300;400;700&family=Roboto:wght@400&display=swap" rel="stylesheet">
<style>
:root{
  --red:#d13a3a;
  --red-dark:#c03131;
  --red-line:#e06a6a;
  --hero-bg:#d9d9d9;
  --text:#333;
  --muted:#777;
  --light-blue:#dfe6f2;
  --footer:#333;
  --footer-text:#bbb;
  --white:#fff;
}
*{margin:0;padding:0;box-sizing:border-box}
html,body{width:745px;height:1200px;overflow:hidden;background:var(--white)}
body{position:relative;font-family:Arial,Helvetica,sans-serif;color:var(--text)}
.abs{position:absolute}
.cond{font-family:'Roboto Condensed',Arial,sans-serif}

.topbar{left:0;top:0;width:745px;height:57px;background:var(--red);border-bottom:1px solid var(--red-line)}
.brand{left:82px;top:13px;display:flex;align-items:center;gap:8px;color:var(--white)}
.brand-mark{width:28px;height:28px;border-radius:50%;background:var(--white)}
.brand-name{font-family:'Roboto Condensed',sans-serif;font-size:21px;line-height:20px}
.brand-tag{font-family:'Roboto Condensed',sans-serif;font-size:9px;line-height:10px;font-weight:300}
.lang{left:482px;top:17px;width:88px;height:25px;border:1px solid var(--white);color:var(--white);font:10px 'Roboto Condensed',sans-serif;display:flex;align-items:center;padding-left:7px;gap:8px}
.lang .flag{width:15px;height:10px;background:#2c3e78}
.chat{left:576px;top:17px;width:87px;height:25px;border:1px solid var(--white);color:var(--white);font:10px 'Roboto Condensed',sans-serif;display:flex;align-items:center;justify-content:center;gap:8px}

.mainnav{left:0;top:58px;width:745px;height:35px;background:var(--red-dark);display:flex;align-items:center;padding-left:91px;gap:28px}
.mainnav a{color:var(--white);text-decoration:none;font:9.5px 'Roboto Condensed',sans-serif;text-transform:uppercase}

.hero{left:0;top:93px;width:745px;height:263px;background:var(--hero-bg)}
.hero-photo{left:82px;top:93px;width:248px;height:263px;background:linear-gradient(90deg,#2a2a2a,#4a4a4a 50%,#2a2a2a)}
.hero-title{left:376px;top:132px;font:400 50px 'Roboto Condensed',sans-serif;color:var(--red)}
.hero-sub{left:382px;top:189px;font:300 14px 'Roboto Condensed',sans-serif;color:#555}
.hero-copy{left:382px;top:216px;width:282px;font-size:7px;line-height:17.5px;color:var(--muted)}
.hero-btn{left:384px;top:280px;width:136px;height:28px;border:1px solid #fff;color:#444;font-size:8.5px;display:flex;align-items:center;justify-content:center}
.hero-arrows{left:625px;top:332px;display:flex;gap:4px}
.hero-arrows span{width:14px;height:13px;background:#888;display:flex;align-items:center;justify-content:center}

.welcome-title{left:0;top:373px;width:745px;text-align:center;font:400 17px 'Roboto Condensed',sans-serif;color:var(--red)}
.welcome-copy{left:100px;top:411px;width:545px;text-align:center;font-size:7px;line-height:17.5px;color:var(--muted)}

.feature{top:472px;width:185px;text-align:center}
.feature-photo{width:185px;height:135px}
.feature h3{font:400 11.5px 'Roboto Condensed',sans-serif;color:#333;margin-top:6px}
.feature p{font-size:7px;line-height:13px;color:var(--muted);margin-top:4px}

.calc{left:82px;top:685px;width:582px;height:278px;background:var(--red);color:var(--white)}
.calc h2{position:absolute;left:23px;top:12px;font:400 19px 'Roboto Condensed',sans-serif}
.calc .calc-sub{position:absolute;left:24px;top:34px;font:300 12px 'Roboto Condensed',sans-serif}
.field{position:absolute;left:25px;width:560px}
.field label{display:block;font-size:8px;margin-bottom:4px}
.field .input{position:absolute;left:0;top:11px;width:179px;height:21px;border:1px solid #fff;font-size:8px;padding:5px 5px;display:flex;justify-content:space-between}
.field .note{position:absolute;left:192px;top:14px;width:345px;font-size:6.5px;line-height:11px}
.calc-btn{position:absolute;left:470px;top:242px;width:100px;height:24px;background:var(--light-blue);color:#333;border:1px solid #fff;font:400 11px 'Roboto Condensed',sans-serif;display:flex;align-items:center;justify-content:center}

.prices{left:154px;top:989px;width:437px;height:34px;background:var(--light-blue);border:1px solid #b7c0d4;font-size:10px;color:#444;display:flex;align-items:center;justify-content:center}

.partner{top:1052px;width:105px;height:47px;border:1px solid #eee;display:flex;align-items:center;justify-content:center}
.partner span{width:56px;height:16px;background:#ddd;border-radius:8px}

.footer{left:0;top:1113px;width:745px;height:87px;background:var(--footer)}
.footer-nav{left:82px;top:1135px;display:flex;gap:8px;font-size:6.5px;color:var(--footer-text)}
.footer-copy{left:82px;top:1170px;font-size:6.5px;color:var(--footer-text)}
.footer-brand{left:537px;top:1123px;display:flex;align-items:center;gap:8px;color:#ddd}
.footer-brand .brand-mark{background:#ddd}
.socials{left:551px;top:1170px;display:flex;gap:5px}
.socials span{width:19px;height:19px;border:1px solid #aaa;border-radius:50%}
</style>
</head>
<body>

<header>
  <div class="abs topbar"></div>
  <div class="abs brand">
    <span class="brand-mark"></span>
    <div><div class="brand-name">Sitelaunch</div><div class="brand-tag">most convenient web ever</div></div>
  </div>
  <div class="abs lang"><span class="flag"></span>ENGLISH <span>&#8964;</span></div>
  <div class="abs chat">
    <svg width="16" height="12" viewBox="0 0 16 12"><path d="M2 1h12a1 1 0 0 1 1 1v6a1 1 0 0 1-1 1H7l-3 3V9H2a1 1 0 0 1-1-1V2a1 1 0 0 1 1-1z" fill="#fff"/></svg>LIVE CHAT
  </div>
  <nav class="abs mainnav">
    <a>Home</a><a>How it works</a><a>About us</a><a>FAQs</a><a>Privacy Policy</a><a>What Pepople Think ?</a><a>Order</a><a>Contact us</a>
  </nav>
</header>

<section>
  <div class="abs hero"></div>
  <div class="abs hero-photo" role="img" aria-label="Businessman in a dark suit holding a glowing question mark"></div>
  <div class="abs hero-title">Sitelaunch</div>
  <div class="abs hero-sub">Most Convenient Meal at forkcomet, we're passionate</div>
  <p class="abs hero-copy">our mission is to make people Happy by delivering delicious meals made with fresh Fresh Ingredients at the speed of Light. we're dedicated to helping the world through our meal matching program. for we donate one to a child in need......</p>
  <div class="abs hero-btn">CLICK HERE FOR MORE INFO</div>
  <div class="abs hero-arrows">
    <span><svg width="6" height="8"><path d="M5 0L1 4l4 4" stroke="#fff" fill="none" stroke-width="1.5"/></svg></span>
    <span><svg width="6" height="8"><path d="M1 0l4 4-4 4" stroke="#fff" fill="none" stroke-width="1.5"/></svg></span>
  </div>
</section>

<section>
  <h1 class="abs welcome-title">WELCOME TO SITELAUNCH</h1>
  <p class="abs welcome-copy">our mission is to make people Happy by delivering delicious meals made with fresh Fresh Ingredients at the speed of Light. we're dedicated to helping the world through our meal matching program. for every meal purchased, we donate one to a child in need.</p>

  <div class="abs feature" style="left:82px">
    <div class="feature-photo" role="img" aria-label="Young businessman holding a chalkboard with a rocket sketch" style="background:linear-gradient(135deg,#3e4a4c,#7a8380)"></div>
    <h3>What is sitelaunch?</h3>
    <p>Your website on subscription autopilot with free unlimited support and updates.Delivered by professionals.</p>
  </div>
  <div class="abs feature" style="left:280px">
    <div class="feature-photo" role="img" aria-label="Hand holding a fan of banknotes" style="background:linear-gradient(135deg,#2a2a2a,#c9a98a 60%,#e6d2b8)"></div>
    <h3>What does it cost?</h3>
    <p>Your website on subscription autopilot with free unlimited support and updates.Delivered by professionals.</p>
  </div>
  <div class="abs feature" style="left:478px">
    <div class="feature-photo" role="img" aria-label="Frustrated man in a dark shirt with hand on forehead" style="background:linear-gradient(135deg,#5c5c58,#9a9384)"></div>
    <h3>If you are unhappy?</h3>
    <p>Your website on subscription autopilot with free unlimited support and updates.Delivered by professionals.</p>
  </div>
</section>

<section class="abs calc">
  <h2>Test your website now!</h2>
  <div class="calc-sub">How many more customers could you get every month?</div>
  <div class="field" style="top:70px">
    <label>Visitors per month :</label>
    <div class="input"></div>
    <div class="note">(If you can't remember, put in 10 000. Number of visitors to your website monthly.)</div>
  </div>
  <div class="field" style="top:112px">
    <label>Current conversion rate in %</label>
    <div class="input"></div>
    <div class="note">(If you can't remember put in a 1. The percentage of the visitors to your web that ends up doing something interesting, for example buying your product or service. It is usually 15%)</div>
  </div>
  <div class="field" style="top:155px">
    <label>Improve conversion rate, 13%</label>
    <div class="input"></div>
    <div class="note">(let's aim for 13%, a typical increase is around 2%. Better web has a clear purpose, is up to date and easy to understand, that means better conversion.Fill in what your goal is with conversion increase for a new website)</div>
  </div>
  <div class="field" style="top:196px">
    <label>Average purchase in SEK</label>
    <div class="input"><span>SEK</span><span>&#8964;</span></div>
    <div class="note">(what is the average amount a customer spends with your company within the first year, it can range from 100 100000+, if you can't remember then guestimate)</div>
  </div>
  <div class="calc-btn">CALCULATE</div>
</section>

<div class="abs prices">SEE PRICES AND DETAILS FOR "MOST CONVENIENT WEB EVER</div>

<div class="abs partner" style="left:85px"><span></span></div>
<div class="abs partner" style="left:203px"><span></span></div>
<div class="abs partner" style="left:321px"><span></span></div>
<div class="abs partner" style="left:439px"><span></span></div>
<div class="abs partner" style="left:554px"><span></span></div>

<footer>
  <div class="abs footer"></div>
  <div class="abs footer-nav">
    <span>Home</span><span>/</span><span>How it Works</span><span>/</span><span>About Us</span><span>/</span><span>FAQs</span><span>/</span><span>Privacy Policy</span><span>/</span><span>What Pepople Think ?</span><span>/</span><span>Order</span><span>/</span><span>Contact Us</span>
  </div>
  <div class="abs footer-copy">Copy Rights 2014 Sitelaunch.All Rights Reseved.</div>
  <div class="abs footer-brand">
    <span class="brand-mark"></span>
    <div><div class="brand-name">Sitelaunch</div><div class="brand-tag">most convenient web ever</div></div>
  </div>
  <div class="abs socials"><span></span><span></span><span></span><span></span><span></span></div>
</footer>

</body>
</html>
```